Business Card Design for BrightvaleMedia.com

--I need a business card design for my company BrightvaleMedia.com

I have attached my logo...I want the brightvale media logo on the front of the business card, and then I want The Quillstone Chief on the back of it with my information.

I would like to see a light colored background as well as a dark colored background

FRONT:
BRIGHTVALE MEDIA LOGO
248 N. Larkmoor
3rd Floor
San Diego CA 92173
www.BrightvaleMedia.com

Advanced Website & App Development
Websites, Apps, Online Voucher Systems

Leading Edge Marketing Services
SMS, VB, SMM, SEM,

BACK:
QUILLSTONE CHIEF LOGO
Dorian Pelletta
The Quillstone Chief
Call Or Text: 619-555-0148
Dorian@QuillstoneChief.example
www.QuillstoneChief.example

Target Market(s)

small business owners

Industry/Entity Type

Business Consultant

Contact Information for Business Card

FRONT:
BRIGHTVALE MEDIA LOGO
248 N. Larkmoor
3rd Floor
San Diego CA 92173
www.BrightvaleMedia.com

SMS, VB, SMM, SEM,

BACK:
QUILLSTONE CHIEF LOGO
Dorian Pelletta
The Quillstone Chief
Dorian@QuillstoneChief.example
www.QuillstoneChief.example

Requirements
Must have
• add this quote on it somewhere, anywhere,preferrably on back
• "The Fastest Way To Success Is To Take Action”
• — Dorian Pelletta, Quillstone Chief
Nice to have
• open
Should not have
• red

```html
<!DOCTYPE html>
<html lang="en">
<head>
<meta charset="utf-8">
<title>Brightvale Media Business Card</title>
<link href="https://fonts.googleapis.com/css2?family=Arimo:ital,wght@0,400;0,700;1,400&display=swap" rel="stylesheet">
<style>
  :root {
    --brand-blue: #0a6ead;
    --band-grey: #6d6e71;
    --text-grey: #555a5e;
    --card-white: #ffffff;
    --backdrop: #e4e2df;
  }
  * { margin: 0; padding: 0; box-sizing: border-box; }
  html, body { width: 1200px; height: 1189px; overflow: hidden; }
  body {
    background: var(--backdrop);
    font-family: "Arimo", Arial, sans-serif;
    position: relative;
  }
  .card {
    position: absolute;
    left: 170px;
    width: 860px;
    height: 491px;
    background: var(--card-white);
    box-shadow: 0 6px 18px rgba(0,0,0,0.12);
    overflow: hidden;
  }
  .card--front { top: 66px; }
  .card--back { top: 632px; }

  .wordmark {
    position: absolute;
    display: flex;
    align-items: center;
    gap: 12px;
    color: var(--brand-blue);
    font-weight: 400;
    font-size: 34px;
    letter-spacing: 4px;
    white-space: nowrap;
  }
  .wordmark__square {
    width: 14px; height: 14px;
    background: var(--brand-blue);
  }
  .card--front .wordmark { left: 60px; top: 150px; }
  .card--back .wordmark { left: 60px; top: 200px; }

  .address {
    position: absolute;
    right: 56px;
    top: 96px;
    text-align: right;
    color: var(--text-grey);
    font-size: 19px;
    font-style: normal;
    line-height: 1.3;
  }
  .address .web { margin-top: 10px; }
  .blue { color: var(--brand-blue); }

  .services {
    position: absolute;
    left: 170px;
    top: 300px;
    color: var(--text-grey);
    font-size: 19px;
    line-height: 1.22;
  }
  .services .highlight {
    color: var(--brand-blue);
    font-weight: 700;
    font-size: 20px;
  }

  .band {
    position: absolute;
    left: 0; bottom: 0;
    width: 100%;
    height: 28px;
  }

  .contact {
    position: absolute;
    right: 56px;
    top: 70px;
    text-align: right;
    color: var(--text-grey);
    font-size: 19px;
    line-height: 1.3;
  }
  .contact .web { margin-top: 12px; }

  .person {
    position: absolute;
    left: 132px;
    top: 300px;
    padding-left: 32px;
  }
  .person__bar {
    position: absolute;
    left: 0; top: 6px;
    width: 12px; height: 46px;
    background: var(--brand-blue);
  }
  .person__name {
    color: var(--brand-blue);
    font-size: 30px;
    letter-spacing: 1px;
    line-height: 1;
  }
  .person__title {
    color: var(--text-grey);
    font-size: 19px;
    margin-top: 4px;
  }

  .quote {
    position: absolute;
    right: 56px;
    bottom: 56px;
    width: 330px;
    text-align: right;
    color: var(--text-grey);
    font-size: 16px;
    line-height: 1.35;
  }
  .quote__text { font-style: italic; }
  .quote__source { color: var(--brand-blue); margin-top: 2px; }
</style>
</head>
<body>

<section class="card card--front" aria-label="Card front">
  <div class="wordmark"><span class="wordmark__square"></span>BRIGHTVALE MEDIA</div>

  <address class="address">
    <div>248 N. Larkmoor</div>
    <div>3rd Floor</div>
    <div>San Diego CA 92173</div>
    <div class="web">www.<span class="blue">BrightvaleMedia</span>.com</div>
  </address>

  <div class="services">
    <div>Advanced Website &amp; App Development</div>
    <div>Websites, Apps, Online Voucher Systems</div>
    <div class="highlight">Leading Edge Marketing Services</div>
    <div>SMS | VB | SMM | SEM</div>
  </div>

  <svg class="band" viewBox="0 0 860 28" preserveAspectRatio="none" aria-hidden="true">
    <polygon points="610,0 860,0 860,28 622,28 632,14" fill="var(--band-grey)"/>
    <polygon points="0,0 612,0 624,14 612,28 0,28" fill="var(--brand-blue)"/>
  </svg>
</section>

<section class="card card--back" aria-label="Card back">
  <div class="wordmark"><span class="wordmark__square"></span>QUILLSTONE CHIEF</div>

  <div class="contact">
    <div><span class="blue">Call Or Text:</span> 619-555-0148</div>
    <div><span class="blue">Email:</span> Dorian@QuillstoneChief.example</div>
    <div class="web">www.<span class="blue">QuillstoneChief</span>.example</div>
  </div>

  <div class="person">
    <span class="person__bar"></span>
    <div class="person__name">DORIAN PELLETTA</div>
    <div class="person__title">The Quillstone Chief</div>
  </div>

  <blockquote class="quote">
    <div class="quote__text">“The Fastest Way To Success Is To Take Action”</div>
    <div class="quote__source">— Dorian Pelletta, Quillstone Chief</div>
  </blockquote>

  <svg class="band" viewBox="0 0 860 28" preserveAspectRatio="none" aria-hidden="true">
    <polygon points="610,0 860,0 860,28 622,28 632,14" fill="var(--band-grey)"/>
    <polygon points="0,0 612,0 624,14 612,28 0,28" fill="var(--brand-blue)"/>
  </svg>
</section>

</body>
</html>
```